New Zealand Marlborough Sauvignon Blanc wine packaging design

We need packaging design for our new wine brand, Dunmore Vale. The wine is a New Zealand Marlborough Sauvignon Blanc. We would like the packaging will portray elegance and style with an understated label. We are looking for a label that portrays the elegance of the French Riviera. The label should be round or pill shaped.
Updates

Industry/Entity Type

Wine

Font styles to use
Serif
Sans Serif

Requirements
Must have
• The words in order of importance: Dunmore Vale, Sauvignon Blanc, Marlborough, New Zealand. It should be fit to the bottle posted in the links
Nice to have
• a pill shape or circular shape
Should not have
• Illustrations of wine bottles, wine glasses, or grapes

```html
<!DOCTYPE html>
<html lang="en">
<head>
<meta charset="utf-8">
<title>Dunmore Vale Sauvignon Blanc – Label</title>
<link href="https://fonts.googleapis.com/css2?family=Lora:wght@400&family=Ephesis&display=swap" rel="stylesheet">
<style>
  :root {
    --backdrop: #341a1c;
    --label-paper: #ffffff;
    --copper: #b5603a;
    --copper-deep: #9c3f22;
    --ink-brown: #5a4640;
    --sky: #c3d5e8;
    --sea-light: #a9c0e0;
    --sea-deep: #84a3cc;
  }
  * { margin: 0; padding: 0; box-sizing: border-box; }
  html, body {
    width: 849px;
    height: 1200px;
    overflow: hidden;
    background: var(--backdrop);
  }
  .canvas {
    position: relative;
    width: 849px;
    height: 1200px;
    display: flex;
    align-items: center;
    justify-content: center;
  }
  .wine-label {
    width: 600px;
    height: 795px;
    display: block;
  }
  .label-body { fill: var(--label-paper); }
  .label-rule { fill: none; stroke: var(--copper); stroke-width: 1; }
  .region-arc {
    font-family: 'Lora', serif;
    font-size: 14px;
    letter-spacing: 2.6px;
    fill: var(--ink-brown);
  }
  .brand-name {
    font-family: 'Ephesis', cursive;
    font-size: 68px;
    fill: var(--copper-deep);
  }
  .varietal {
    font-family: 'Lora', serif;
    font-size: 19px;
    fill: #ffffff;
  }
</style>
</head>
<body>
<main class="canvas">
  <svg class="wine-label" viewBox="0 0 400 530" xmlns="http://www.w3.org/2000/svg">
    <defs>
      <linearGradient id="sea-fade" x1="0" y1="0" x2="0" y2="1">
        <stop offset="0" stop-color="var(--sea-light)"/>
        <stop offset="1" stop-color="var(--sea-deep)"/>
      </linearGradient>
      <path id="arc-top" d="M92 68 Q200 18 308 68"/>
      <path id="arc-bottom" d="M92 470 Q200 536 308 470"/>
    </defs>

    <rect class="label-body" x="0" y="0" width="400" height="530" rx="200" ry="200"/>
    <rect class="label-rule" x="7" y="7" width="386" height="516" rx="193" ry="193"/>

    <path class="coast-scene" role="img" aria-label="Palm trees on a white shore under a pale blue sky"
          fill="var(--sky)"
          d="M50 290 V208 A150 150 0 0 1 350 208 V290 C320 285 280 283 240 287 C200 291 150 282 110 286 C80 289 62 290 50 290 Z"/>

    <text class="region-arc"><textPath href="#arc-top" startOffset="50%" text-anchor="middle">MARLBOROUGH</textPath></text>

    <text class="brand-name" x="200" y="352" text-anchor="middle">Dunmore Vale</text>

    <path class="sea-bowl" role="img" aria-label="Soft blue sea with distant hills"
          fill="url(#sea-fade)"
          d="M62 380 C110 372 150 380 200 376 C250 372 290 380 338 378 A138 92 0 0 1 62 380 Z"/>

    <text class="varietal" x="200" y="416" text-anchor="middle">Sauvignon Blanc</text>

    <text class="region-arc"><textPath href="#arc-bottom" startOffset="50%" text-anchor="middle">NEW ZEALAND</textPath></text>
  </svg>
</main>
</body>
</html>
```